International Clinical Software Company needs a new business card design

We are looking for a new business card design for our company that has recently expanded into the UK market, making us a multinational company.
After having rebranded our website and produced a new style guide, we are looking for a business card that is creative and attention grabbing, while being consistent with the style and colour scheme used on the new website, www.plumvora.example
We produce care management technology for the aged care market, but the main aspect we aim to communicate is the human element of our software, and the way it assists in providing better care for aged people, and stronger relationships between aged people and the staff that care for them.
Our current business card is a dark green with gold text, which makes the text quite difficult to read, not very aesthetically appealing and the colour scheme looks quite dated.
We would like something fresh and modern, that can still be colourful but doesn't use large blocks of dark colour, and uses the colours within our logo.
Something tying in with the leaves that are used in our logo could work quite nicely, along with the Autumn/Fall colours of soft greens, yellows and reds (also in our existing logo). However also happy to look at fresh, completely out of the box ideas we may not have yet considered.
Target Market(s)
The people that receive this business card work in the aged card or health industry and are either corporate/management level staff or clinical (Registered Nurses, care workers etc.)
Industry/Entity Type
Health Product
Contact Information for Business Card
Company Name - BrindlewayCare
Company locations: United Kingdom, Australia, New Zealand
Staff Details:
Staff name: Derek Mallow
Staff job title: Executive Chairman
Staff email: d.mallow@plumvora.example
Office phone number: 01742 918576
Font styles to use
Other font styles liked:
- Calibri
Requirements
Must have
- Must include the BrindlewayCare brand name in it's current font
- Must include logo (3 leaves in gold circle)
- Must include Business Card Details
Nice to have
- Elements of gold
- White space
- Something autumn themed but not too cliched
Should not have
- No blue - used by a major competitor and we would like to differentiate from them
- Large blocks of dark green colour (the green that appears in our leaves on the logo on our current business card is the background colour and it is far too dark)

```html
<!DOCTYPE html>
<html lang="en">
<head>
<meta charset="utf-8">
<title>BrindlewayCare business card</title>
<link rel="stylesheet" href="https://fonts.googleapis.com/css2?family=Open+Sans:wght@300;400;700&display=swap">
<style>
  :root {
    --page: #ece8e1;
    --card: #ffffff;
    --leaf-green: #5e9638;
    --olive: #b9b735;
    --olive-light: #d6d14a;
    --gold-soft: #cfc39f;
    --gold-text: #c8bf62;
    --ink-green: #5e9638;
  }
  * { margin: 0; padding: 0; box-sizing: border-box; }
  html, body { width: 1200px; height: 1022px; overflow: hidden; }
  body {
    background: var(--page);
    font-family: "Open Sans", Arial, sans-serif;
    position: relative;
  }
  .card {
    position: absolute;
    left: 75px; top: 211px;
    width: 1050px; height: 600px;
    background: var(--card);
    border-radius: 18px;
    overflow: hidden;
    box-shadow: 0 6px 24px rgba(0,0,0,0.12);
  }
  .card__swoosh { position: absolute; inset: 0; width: 100%; height: 100%; }
  .brand {
    position: absolute;
    right: 70px; top: 70px;
    display: flex; flex-direction: column; align-items: flex-end; gap: 18px;
  }
  .brand__dot {
    width: 130px; height: 130px; border-radius: 50%;
    background: var(--gold-soft);
  }
  .brand__name {
    font-weight: 300;
    font-size: 66px;
    color: var(--gold-soft);
    letter-spacing: 1px;
    line-height: 1;
  }
  .person { position: absolute; left: 70px; top: 120px; }
  .person__name {
    font-weight: 700; font-size: 34px; color: var(--olive);
    text-transform: uppercase; letter-spacing: 0.5px;
  }
  .person__title { font-size: 24px; color: var(--ink-green); margin-top: 2px; }
  .contact { position: absolute; left: 110px; top: 236px; list-style: none; }
  .contact__item {
    display: flex; align-items: center; gap: 14px;
    font-size: 22px; color: var(--gold-text); line-height: 38px;
  }
  .contact__icon { width: 20px; height: 20px; flex: none; }
  .locations {
    position: absolute; left: 170px; top: 350px;
    font-size: 22px; color: var(--gold-text); line-height: 32px;
  }
</style>
</head>
<body>
  <section class="card">
    <svg class="card__swoosh" viewBox="0 0 1050 600" preserveAspectRatio="none" aria-hidden="true">
      <defs>
        <linearGradient id="oliveBand" x1="0" y1="1" x2="1" y2="0">
          <stop offset="0" stop-color="#b3b232"/>
          <stop offset="1" stop-color="#d8d24c"/>
        </linearGradient>
      </defs>
      <path d="M0,470 C450,500 820,450 1050,330 L1050,600 L0,600 Z" fill="var(--leaf-green)"/>
      <path d="M0,505 C470,535 840,490 1050,372 L1050,600 L0,600 Z" fill="#ffffff"/>
      <path d="M0,512 C470,542 840,498 1050,380 L1050,600 L0,600 Z" fill="url(#oliveBand)"/>
    </svg>

    <div class="brand">
      <span class="brand__dot" aria-hidden="true"></span>
      <span class="brand__name">BrindlewayCare</span>
    </div>

    <div class="person">
      <h1 class="person__name">Derek Mallow</h1>
      <p class="person__title">Executive Chairman</p>
    </div>

    <ul class="contact">
      <li class="contact__item">
        <svg class="contact__icon" viewBox="0 0 24 24" aria-hidden="true"><path fill="var(--ink-green)" d="M6.6 10.8a15 15 0 0 0 6.6 6.6l2.2-2.2c.3-.3.7-.4 1-.2 1.1.4 2.3.6 3.6.6.6 0 1 .4 1 1V20c0 .6-.4 1-1 1A17 17 0 0 1 3 4c0-.6.4-1 1-1h3.5c.6 0 1 .4 1 1 0 1.3.2 2.5.6 3.6.1.3 0 .7-.2 1z"/></svg>
        <span>01742 918576</span>
      </li>
      <li class="contact__item">
        <svg class="contact__icon" viewBox="0 0 24 24" aria-hidden="true"><rect x="2" y="5" width="20" height="14" rx="1.5" fill="none" stroke="var(--ink-green)" stroke-width="2"/><path d="M3 6l9 7 9-7" fill="none" stroke="var(--ink-green)" stroke-width="2"/></svg>
        <span>d.mallow@plumvora.example</span>
      </li>
    </ul>

    <div class="locations">
      <p>United Kingdom</p>
      <p>Australia, New Zealand</p>
    </div>
  </section>
</body>
</html>
```